Business Card Design - Photographer

I am a landscape photographer and I require a business card design. 

I require two designs:
1)  a double sided business card
 and
b)  a single sided business card 

The single sided design can either be the same as the double sided (with just one side having all the information)....or it can be an entire new design. Its up to you.

My corporate colours are (CMYK):

Blue   69, 32, 0, 0
Grey  72,  64,  47,  31
Green  32,  2,  91,  0
Yellow   0, 19, 92, 0
Orange  0, 39, 75, 0

Colour space in final file should be in CMYK.

The details that need to be included on the card:

- Use the provided Logo
- Name: Wiktor Baranowski
- Email:   sales@vistalumeworks.com.au
- Website:    vistalumeworks.com.au
- Twitter:    twitter.com/vistalumeworks
- Facebook:   facebook.com/vistalumeworks
- Mobile  0417 539 662

Please use the attached template to design the logo to the specified size, including the marked bleed lines. I have also attached my logo in PNG (transparent background) and ai format for you to use.

The final file should be:
- Photoshop version with layers so I can edit the name/text etc. All non vector files should be high resolution at 1039 x 697 pixels at 300 dpi.

I also require a file as:
- Vector based PDF

Anyway questions please contact me.

Thank you

Industry/Entity Type

Landscape

Logo styles of interest
Pictorial/Combination Logo
Abstract Logo
Wordmark Logo
Lettermark Logo
Requirements
Must have
• The details that need to be included on the card:

- Use the provided Logo
- Name: Wiktor Baranowski
- Email: sales@vistalumeworks.com.au
- Website: vistalumeworks.com.au
- Twitter: twitter.com/vistalumeworks
- Facebook: facebook.com/vistalumeworks
- Mobile 0417 539 662

```html
<!DOCTYPE html>
<html lang="en">
<head>
<meta charset="utf-8">
<title>Vistalume Works – Business Cards</title>
<link href="https://fonts.googleapis.com/css2?family=Cinzel:wght@600&family=Tinos&family=Open+Sans:wght@400&display=swap" rel="stylesheet">
<style>
  :root {
    --backdrop: #ebe7e1;
    --card: #ffffff;
    --ink: #3b3f4e;
    --text: #2e2e33;
    --muted: #8f9199;
    --blue: #3f96d5;
    --blue-soft: #a9cbe8;
    --green-soft: #d4e4a6;
    --peach-soft: #f8d2b0;
    --grey-soft: #a9abb2;
    --yellow-soft: #fbe3a0;
  }
  * { margin: 0; padding: 0; box-sizing: border-box; }
  html, body { width: 1200px; height: 1028px; overflow: hidden; background: var(--backdrop); }
  .canvas { position: relative; width: 1200px; height: 1028px; }

  .card {
    position: absolute;
    width: 755px; height: 428px;
    background: var(--card);
    border-radius: 22px;
    border: 1px solid #d6d2cc;
    box-shadow: 0 2px 6px rgba(0,0,0,0.12);
    overflow: hidden;
  }
  .card--front { left: 57px; top: 65px; }
  .card--back  { left: 366px; top: 536px; }

  .brand-mark {
    position: absolute;
    border-radius: 50%;
    background: var(--ink);
  }
  .brand-name {
    position: absolute;
    font-family: "Cinzel", serif;
    font-weight: 600;
    color: var(--ink);
    white-space: nowrap;
  }

  /* front */
  .card--front .brand-mark { left: 132px; top: 30px; width: 110px; height: 110px; }
  .card--front .brand-name { left: 36px; top: 146px; font-size: 29px; letter-spacing: 0.5px; }

  .contact-list {
    position: absolute; left: 36px; top: 234px;
    list-style: none;
    font-family: "Tinos", serif;
    font-size: 19px;
    color: var(--text);
  }
  .contact-list li { display: flex; align-items: center; height: 26.5px; }
  .contact-list svg { width: 13px; height: 13px; margin-right: 5px; flex: none; }
  .address {
    position: absolute; left: 36px; top: 381px;
    font-family: "Tinos", serif; font-size: 19px; color: var(--text);
  }
  .tree-art {
    position: absolute; right: 0; top: 0;
    width: 245px; height: 100%;
    background:
      radial-gradient(circle at 60% 30%, var(--blue-soft) 0 18%, transparent 40%),
      radial-gradient(circle at 40% 60%, var(--peach-soft) 0 16%, transparent 38%),
      radial-gradient(circle at 75% 65%, var(--grey-soft) 0 14%, transparent 36%),
      radial-gradient(circle at 30% 15%, var(--green-soft) 0 12%, transparent 32%),
      radial-gradient(circle at 70% 45%, var(--yellow-soft) 0 14%, transparent 34%),
      #ffffff;
  }

  /* back */
  .card--back .brand-mark { left: 316px; top: 74px; width: 122px; height: 122px; }
  .card--back .brand-name { left: 0; width: 100%; text-align: center; top: 230px; font-size: 34px; letter-spacing: 0.5px; }
  .back-web {
    position: absolute; left: 0; width: 100%; top: 350px; text-align: center;
    font-family: "Open Sans", sans-serif; font-size: 18px; letter-spacing: 3.5px; color: var(--text);
  }
</style>
</head>
<body>
<main class="canvas">
  <section class="card card--front">
    <div class="brand-mark" aria-hidden="true"></div>
    <div class="brand-name">VISTALUME WORKS</div>
    <ul class="contact-list">
      <li><svg viewBox="0 0 12 12"><rect x="3" y="1" width="6" height="10" rx="1.2" fill="var(--muted)"/></svg>0417 539 662</li>
      <li><svg viewBox="0 0 12 12"><rect x="1" y="3" width="10" height="6" fill="var(--muted)"/></svg>sales@vistalumeworks.com.au</li>
      <li><svg viewBox="0 0 12 12"><circle cx="6" cy="6" r="4.5" fill="var(--muted)"/></svg>www.vistalumeworks.com.au</li>
      <li><svg viewBox="0 0 12 12"><rect x="1" y="1" width="10" height="10" rx="2" fill="var(--blue)"/></svg>vistalumeworks</li>
      <li><svg viewBox="0 0 12 12"><rect x="1" y="1" width="10" height="10" rx="2" fill="#3b5998"/></svg>vistalumeworks</li>
    </ul>
    <div class="address">00, Complex Name, State Name, City 0020</div>
    <div class="tree-art" role="img" aria-label="Stylised grey tree with pastel leaves in blue, peach, green, yellow and grey"></div>
  </section>

  <section class="card card--back">
    <div class="brand-mark" aria-hidden="true"></div>
    <div class="brand-name">VISTALUME WORKS</div>
    <div class="back-web">www.vistalumeworks.com.au</div>
  </section>
</main>
</body>
</html>
```